Boutique custom software development company needs new business card

Our nearly 20 year old custom software development company would like to better include the fact that we are now providing Bitcoin services. These new services are B2B include education (how to acquire and securely hold Bitcoin) and integrating Bitcoin payments into existing ecommerce sites or other existing systems. Please keep the card clean and simple. Attached is our current design and some other files. vextorial.com

Target Market(s)

businesses owners interested in long term relationship

Industry/Entity Type

Custom software development and Bitcoin

Contact Information for Business Card

Dale Parker, dale@vextorial.com, vextorial.com, (888) 555-VXTRL

Font styles to use
Other font styles liked:
• monospace

Requirements
Must have
• double-sided
Nice to have
• clean and simple
Should not have
• physical address

```html
<!DOCTYPE html>
<html lang="en">
<head>
<meta charset="utf-8">
<title>Vextorial — Business Card</title>
<link href="https://fonts.googleapis.com/css2?family=Poppins:wght@400;600;700&family=Lato:wght@400;700&display=swap" rel="stylesheet">
<style>
  :root {
    --backdrop: #2b2c2e;
    --card: #1b1c1e;
    --orange: #f07a1c;
    --blue: #3f72c4;
    --white: #f2f2f2;
    --rule: #8a8a8a;
  }
  * { margin: 0; padding: 0; box-sizing: border-box; }
  html, body { width: 1200px; height: 1108px; overflow: hidden; }
  body {
    background: var(--backdrop);
    font-family: "Poppins", sans-serif;
    position: relative;
  }
  .card {
    position: absolute;
    top: 250px;
    width: 380px;
    height: 600px;
    background: var(--card);
    border-radius: 22px;
    overflow: hidden;
    box-shadow: 0 18px 40px rgba(0,0,0,.45);
  }
  .card--front { left: 170px; }
  .card--back { left: 650px; }

  .brand {
    position: absolute;
    top: 120px;
    left: 0; right: 0;
    text-align: center;
  }
  .brand__name {
    font-family: "Poppins", sans-serif;
    font-weight: 700;
    font-size: 54px;
    letter-spacing: 1px;
    color: var(--blue);
    line-height: 1;
  }
  .brand__tagline {
    margin-top: 10px;
    font-family: "Lato", sans-serif;
    font-size: 19px;
    color: var(--blue);
  }
  .brand__services {
    margin-top: 6px;
    font-family: "Lato", sans-serif;
    font-size: 16px;
    color: var(--orange);
    letter-spacing: .3px;
  }

  .person {
    position: absolute;
    top: 385px;
    left: 0; right: 0;
    text-align: center;
    font-weight: 700;
    font-size: 27px;
    letter-spacing: .5px;
  }
  .person__first { color: var(--orange); }
  .person__last { color: var(--blue); }

  .icon-row {
    position: absolute;
    top: 440px;
    left: 40px; right: 40px;
    display: flex;
    align-items: center;
    gap: 8px;
  }
  .icon-row__rule { flex: 1; height: 1px; background: var(--rule); }
  .icon {
    width: 30px; height: 30px;
    background: var(--blue);
    border-radius: 4px;
    display: flex; align-items: center; justify-content: center;
  }

  .contact {
    position: absolute;
    top: 486px;
    left: 0; right: 0;
    text-align: center;
    color: var(--white);
    font-size: 17px;
    line-height: 1.5;
  }

  .back__pattern {
    position: absolute;
    inset: 0;
    background: linear-gradient(135deg, #0c0c0d 0%, #1c1d1f 45%, #4a4b4e 100%);
  }
  .back__name {
    position: absolute;
    left: 0; right: 0;
    top: 410px;
    text-align: center;
    font-weight: 700;
    font-size: 40px;
    color: var(--orange);
  }
</style>
</head>
<body>
  <section class="card card--front">
    <div class="brand">
      <div class="brand__name">Vextorial</div>
      <div class="brand__tagline">developer of custom applications</div>
      <div class="brand__services">bitcoin education &amp; payment integration</div>
    </div>

    <div class="person"><span class="person__first">DALE</span> <span class="person__last">PARKER</span></div>

    <div class="icon-row">
      <span class="icon-row__rule"></span>
      <span class="icon" aria-label="phone">
        <svg width="18" height="18" viewBox="0 0 24 24"><path fill="#1b1c1e" d="M6.6 10.8a15 15 0 0 0 6.6 6.6l2.2-2.2c.3-.3.7-.4 1-.2 1.1.4 2.3.6 3.6.6.6 0 1 .4 1 1V20c0 .6-.4 1-1 1A17 17 0 0 1 3 4c0-.6.4-1 1-1h3.5c.6 0 1 .4 1 1 0 1.3.2 2.5.6 3.6.1.3 0 .7-.2 1z"/></svg>
      </span>
      <span class="icon" aria-label="email">
        <svg width="18" height="18" viewBox="0 0 24 24"><rect x="3" y="5" width="18" height="14" rx="1" fill="none" stroke="#1b1c1e" stroke-width="2"/><path d="M3 6l9 7 9-7" fill="none" stroke="#1b1c1e" stroke-width="2"/></svg>
      </span>
      <span class="icon" aria-label="website">
        <svg width="18" height="18" viewBox="0 0 24 24"><circle cx="12" cy="12" r="9" fill="none" stroke="#1b1c1e" stroke-width="2"/><path d="M3 12h18M12 3c3 3 3 15 0 18M12 3c-3 3-3 15 0 18" fill="none" stroke="#1b1c1e" stroke-width="1.6"/></svg>
      </span>
      <span class="icon-row__rule"></span>
    </div>

    <div class="contact">
      <p>(888) 555-VXTRL</p>
      <p>dale@vextorial.com</p>
      <p>www.vextorial.com</p>
    </div>
  </section>

  <section class="card card--back">
    <div class="back__pattern" role="img" aria-label="Glossy tone-on-tone repeating brand pattern across the card back"></div>
    <div class="back__name">Vextorial</div>
  </section>
</body>
</html>
```